Shine Fox Auto Care Business Card

2 side business card design for an auto detailing business

Target Market(s)

Auto detailing

Contact Information for Business Card

Things included

The business name “Shine Fox Auto Care”
Mark Dunrow
(403)271-6094
Battleford, Sk

Services offered - complete interior& exterior detail
- paint correction & protection
- ceramic coating
- trim restore
- auto carpet & seat cleaning

Requirements
Must have
• Colours that are in my logo

Services offered

My name Mark Dunrow
403-271-6094
Battleford, Sk

Not too sure in what order for these ?
Website. Shinefoxautocare.com
Instagram Shinefoxautocare
Email. Shinefoxautoac@mailvento.com

```html
<!DOCTYPE html>
<html lang="en">
<head>
<meta charset="utf-8">
<title>Shine Fox Auto Care – Business Card</title>
<link href="https://fonts.googleapis.com/css2?family=Arimo:wght@400;700&display=swap" rel="stylesheet">
<style>
  :root {
    --backdrop: #0d0d0d;
    --card: #2a2a2b;
    --card-edge: #8f0c10;
    --red: #a3141a;
    --white: #f4f4f4;
    --rule: #5a5a5a;
    --faint: #343435;
  }
  * { margin: 0; padding: 0; box-sizing: border-box; }
  html, body { width: 1200px; height: 820px; overflow: hidden; }
  body {
    background: var(--backdrop);
    font-family: "Arimo", Arial, sans-serif;
    position: relative;
  }
  .card {
    position: absolute;
    top: 255px;
    width: 540px;
    height: 309px;
    background: var(--card);
    border: 2px solid var(--card-edge);
    overflow: hidden;
  }
  .card--front { left: 40px; }
  .card--back { left: 620px; }

  /* Front */
  .brand {
    position: absolute;
    top: 70px;
    left: 250px;
    display: flex;
    align-items: center;
    gap: 12px;
  }
  .brand__dot {
    width: 34px; height: 34px;
    border-radius: 50%;
    background: var(--red);
    flex: none;
  }
  .brand__name {
    color: var(--white);
    font-weight: 700;
    font-size: 22px;
    letter-spacing: 1px;
    text-transform: uppercase;
    line-height: 1.05;
  }
  .divider {
    position: absolute;
    top: 158px;
    left: 215px;
    width: 300px;
    height: 1px;
    background: var(--rule);
  }
  .owner {
    position: absolute;
    top: 146px;
    left: 34px;
    color: var(--red);
    font-size: 21px;
    letter-spacing: 1.5px;
    text-transform: uppercase;
  }
  .contacts {
    position: absolute;
    left: 34px;
    top: 196px;
    list-style: none;
  }
  .contacts li, .socials li {
    display: flex;
    align-items: center;
    gap: 9px;
    color: var(--white);
    font-size: 15px;
    height: 26px;
  }
  .icon {
    width: 18px; height: 18px;
    border-radius: 50%;
    background: var(--red);
    display: flex; align-items: center; justify-content: center;
    flex: none;
  }
  .socials {
    position: absolute;
    right: 30px;
    top: 176px;
    list-style: none;
    text-align: right;
  }
  .socials li { justify-content: flex-end; }

  /* Back */
  .watermark {
    position: absolute;
    left: -40px;
    top: 20px;
    width: 290px;
    height: 290px;
    border-radius: 50%;
    background: var(--faint);
    display: flex; align-items: center; justify-content: center;
  }
  .watermark__name {
    color: #3c3c3d;
    font-weight: 700;
    font-size: 24px;
    text-transform: uppercase;
    text-align: center;
    line-height: 1.1;
  }
  .services {
    position: absolute;
    left: 268px;
    top: 58px;
  }
  .services__title {
    color: var(--white);
    font-weight: 700;
    font-size: 17px;
    text-transform: uppercase;
    margin-bottom: 6px;
  }
  .services__lead {
    color: var(--red);
    font-size: 13px;
    text-transform: uppercase;
    line-height: 1.25;
    margin-bottom: 12px;
  }
  .services__list { list-style: none; }
  .services__list li {
    color: var(--white);
    font-size: 12.5px;
    text-transform: uppercase;
    display: flex; align-items: center; gap: 8px;
    height: 22px;
  }
  .services__list li::before {
    content: "";
    width: 7px; height: 7px;
    border-radius: 50%;
    background: var(--red);
    flex: none;
  }
</style>
</head>
<body>
  <section class="card card--front">
    <div class="brand">
      <span class="brand__dot"></span>
      <span class="brand__name">Shine Fox<br>Auto Care</span>
    </div>
    <div class="divider"></div>
    <p class="owner">Mark Dunrow</p>
    <ul class="contacts">
      <li><span class="icon"><svg width="10" height="10" viewBox="0 0 24 24"><path fill="#fff" d="M6.6 10.8a15 15 0 0 0 6.6 6.6l2.2-2.2c.3-.3.7-.4 1-.2 1.1.4 2.3.6 3.6.6.6 0 1 .4 1 1V20c0 .6-.4 1-1 1A17 17 0 0 1 3 4c0-.6.4-1 1-1h3.5c.6 0 1 .4 1 1 0 1.3.2 2.5.6 3.6.1.3 0 .7-.2 1z"/></svg></span>(403)271-6094</li>
      <li><span class="icon"><svg width="10" height="10" viewBox="0 0 24 24"><path fill="#fff" d="M2 5h20v14H2z"/><path fill="none" stroke="#a3141a" stroke-width="2" d="M2 5l10 8 10-8"/></svg></span>shinefoxautoac@mailvento.com</li>
      <li><span class="icon"><svg width="11" height="11" viewBox="0 0 24 24" fill="none" stroke="#fff" stroke-width="2"><circle cx="12" cy="12" r="9"/><path d="M3 12h18M12 3c3 3 3 15 0 18M12 3c-3 3-3 15 0 18"/></svg></span>www.Shinefoxautocare.com</li>
    </ul>
    <ul class="socials">
      <li>Shinefoxautocare<span class="icon"></span></li>
      <li>Battleford, Sk<span class="icon"><svg width="10" height="10" viewBox="0 0 24 24"><path fill="#fff" d="M12 2a7 7 0 0 0-7 7c0 5 7 13 7 13s7-8 7-13a7 7 0 0 0-7-7zm0 9.5A2.5 2.5 0 1 1 12 6.5a2.5 2.5 0 0 1 0 5z"/></svg></span></li>
    </ul>
  </section>

  <section class="card card--back">
    <div class="watermark">
      <span class="watermark__name">Shine Fox<br>Auto Care</span>
    </div>
    <div class="services">
      <h2 class="services__title">Services Offered</h2>
      <p class="services__lead">Complete Interior &amp;<br>Exterior Detail</p>
      <ul class="services__list">
        <li>Ceramic Coating</li>
        <li>Trim Restore</li>
        <li>Paint Correction &amp; Protection</li>
        <li>Auto Carpet &amp; Seat Cleaning</li>
      </ul>
    </div>
  </section>
</body>
</html>
```